Card design for orthopaedic surgeons working as The Brightwater Joint Centre

Business cards, letterhead

Colors

Designer to choose colors to be used in the design.

Requirements
Must have
• Late addition.
• Cards letterhead must have logos of
• Crestmoor Lindell College of Surgeons
• Varenwood Bone Health Association
Nice to have
• Back of card to have space for appointment time to be added by hand and some blank space for writing incidental other notes.

```html
<!DOCTYPE html>
<html lang="en">
<head>
<meta charset="utf-8">
<title>The Brightwater Joint Centre — Business Card</title>
<link rel="stylesheet" href="https://fonts.googleapis.com/css2?family=Montserrat:wght@400;600;700&display=swap">
<style>
  :root {
    --navy: #0b3350;
    --navy-deep: #082a43;
    --navy-light: #0f4664;
    --sky: #4a90c8;
    --ink: #3a3f45;
    --rule: #a9adb2;
    --paper: #ffffff;
    --paper-shade: #eceeef;
    --badge: #c9d3db;
    --backdrop: #e4e6e8;
  }
  * { margin: 0; padding: 0; box-sizing: border-box; }
  html, body { width: 1200px; height: 900px; overflow: hidden; }
  body {
    background: var(--backdrop);
    font-family: "Montserrat", sans-serif;
    position: relative;
  }
  .card {
    position: absolute;
    width: 680px;
    height: 389px;
    left: 260px;
    border-radius: 2px;
    overflow: hidden;
    box-shadow: 0 10px 28px rgba(0,0,0,0.18);
  }
  .card-back {
    top: 40px;
    background: radial-gradient(ellipse at 45% 40%, var(--navy-light), var(--navy-deep) 80%);
    display: flex;
    align-items: center;
    justify-content: center;
  }
  .card-back .brand-name {
    color: #ffffff;
    font-size: 34px;
    font-weight: 400;
    letter-spacing: -0.5px;
  }
  .card-front {
    top: 471px;
    background: linear-gradient(160deg, var(--paper) 40%, var(--paper-shade));
  }
  .card-front .brand-name {
    position: absolute;
    left: 60px;
    top: 112px;
    color: var(--sky);
    font-size: 22px;
    font-weight: 400;
    letter-spacing: -0.3px;
  }
  .holder {
    position: absolute;
    right: 70px;
    top: 66px;
    text-align: right;
  }
  .holder-name {
    color: var(--navy);
    font-size: 28px;
    font-weight: 700;
    line-height: 1.1;
  }
  .holder-role {
    color: var(--ink);
    font-size: 17px;
    font-weight: 400;
  }
  .divider {
    position: absolute;
    left: 60px;
    right: 60px;
    top: 156px;
    height: 1px;
    background: var(--rule);
  }
  .contacts {
    position: absolute;
    right: 60px;
    top: 170px;
    list-style: none;
    text-align: right;
    color: var(--ink);
    font-size: 14px;
    line-height: 24px;
  }
  .contacts li { display: flex; justify-content: flex-end; align-items: center; gap: 8px; }
  .contacts svg { width: 14px; height: 14px; fill: var(--sky); flex: none; }
  .address {
    position: absolute;
    left: 60px;
    top: 226px;
    color: var(--ink);
    font-size: 14px;
    line-height: 22px;
  }
  .memberships {
    position: absolute;
    left: 60px;
    top: 314px;
    display: flex;
    gap: 14px;
  }
  .membership-badge {
    width: 36px;
    height: 36px;
    border-radius: 50%;
    background: var(--badge);
  }
  .wave { position: absolute; inset: 0; width: 100%; height: 100%; }
  .website {
    position: absolute;
    left: 330px;
    bottom: 18px;
    color: #ffffff;
    font-size: 14px;
    letter-spacing: 0.3px;
  }
</style>
</head>
<body>
  <section class="card card-back" aria-label="Card back">
    <span class="brand-name">The Brightwater Joint Centre</span>
  </section>

  <section class="card card-front" aria-label="Card front">
    <svg class="wave" viewBox="0 0 680 389" preserveAspectRatio="none" aria-hidden="true">
      <path d="M190,389 C250,312 380,306 500,288 C600,272 660,254 680,228 L680,389 Z" fill="var(--sky)"/>
      <path d="M202,389 C258,320 386,314 504,297 C602,282 662,266 680,244 L680,389 Z" fill="var(--paper)"/>
      <path d="M210,389 C264,325 390,319 508,302 C604,288 664,272 680,251 L680,389 Z" fill="var(--navy)"/>
    </svg>

    <span class="brand-name">The Brightwater Joint Centre</span>

    <div class="holder">
      <div class="holder-name">Daniel Harlow</div>
      <div class="holder-role">Director</div>
    </div>

    <div class="divider"></div>

    <ul class="contacts">
      <li>555 014 2280
        <svg viewBox="0 0 24 24"><path d="M6.6 10.8a15.1 15.1 0 0 0 6.6 6.6l2.2-2.2a1 1 0 0 1 1-.25 11.4 11.4 0 0 0 3.6.57 1 1 0 0 1 1 1V20a1 1 0 0 1-1 1A17 17 0 0 1 3 4a1 1 0 0 1 1-1h3.5a1 1 0 0 1 1 1c0 1.25.2 2.450.57 3.57a1 1 0 0 1-.25 1z"/></svg>
      </li>
      <li>555 017 3946
        <svg viewBox="0 0 24 24"><path d="M7 2h10a2 2 0 0 1 2 2v16a2 2 0 0 1-2 2H7a2 2 0 0 1-2-2V4a2 2 0 0 1 2-2zm0 3v13h10V5z"/></svg>
      </li>
      <li>hello@brightwaterjoint.example
        <svg viewBox="0 0 24 24"><path d="M2 5h20v14H2zm2 2v.5l8 5 8-5V7z"/></svg>
      </li>
    </ul>

    <div class="address">
      Level 2, 17 Marlow Lane<br>
      Eastbridge, 4102
    </div>

    <div class="memberships">
      <span class="membership-badge" role="img" aria-label="Crestmoor Lindell College of Surgeons membership badge"></span>
      <span class="membership-badge" role="img" aria-label="Varenwood Bone Health Association membership badge"></span>
    </div>

    <span class="website">www.brightwaterjoint.example</span>
  </section>
</body>
</html>
```